Business card design for Brivo Engineering Tandem

We need a new business card design along with all the necessary to place an order. The company is Brivo Engineering Tandem and we recently updated our logo.

```html
<!DOCTYPE html>
<html lang="en">
<head>
<meta charset="utf-8">
<title>Brivo Engineering Tandem – Business Card</title>
<link rel="stylesheet" href="https://fonts.googleapis.com/css2?family=Roboto:wght@400;500;700&display=swap">
<style>
  :root {
    --backdrop: #9a9a9a;
    --card: #0b0b0b;
    --card-edge: #161616;
    --accent: #e8c11f;
    --brand-grey: #9c9c9c;
    --text-light: #c9c9c9;
  }
  * { box-sizing: border-box; margin: 0; padding: 0; }
  html, body { width: 1117px; height: 1200px; overflow: hidden; }
  body {
    background: var(--backdrop);
    font-family: "Roboto", Arial, sans-serif;
    position: relative;
  }
  .card {
    position: absolute;
    left: 108px;
    width: 900px;
    height: 514px;
    background: radial-gradient(ellipse at 40% 30%, var(--card-edge), var(--card) 70%);
    border-left: 11px solid var(--accent);
    border-bottom: 11px solid var(--accent);
  }
  .card--front { top: 50px; }
  .card--back { top: 636px; }

  .brand {
    display: flex;
    align-items: center;
    gap: 14px;
    color: var(--brand-grey);
    font-weight: 700;
    letter-spacing: 0.06em;
    text-transform: uppercase;
    white-space: nowrap;
  }
  .brand__mark { background: var(--accent); flex: none; }

  .card--front .brand {
    position: absolute;
    left: 50%; top: 50%;
    transform: translate(-50%, -50%);
    font-size: 38px;
  }
  .card--front .brand__mark { width: 30px; height: 30px; }

  .card--back .brand {
    position: absolute;
    right: 42px; top: 210px;
    font-size: 21px;
    gap: 10px;
  }
  .card--back .brand__mark { width: 18px; height: 18px; }

  .holder { position: absolute; left: 48px; top: 202px; }
  .holder__name {
    color: var(--accent);
    font-weight: 500;
    font-size: 45px;
    line-height: 1;
  }
  .holder__role {
    color: var(--accent);
    font-weight: 700;
    font-size: 16px;
    letter-spacing: 0.42em;
    margin-top: 12px;
  }
  .divider {
    position: absolute;
    left: 48px; right: 42px; top: 302px;
    height: 1px;
    background: var(--accent);
    opacity: 0.8;
  }
  .contacts {
    position: absolute;
    left: 48px; top: 340px;
    list-style: none;
  }
  .contacts li {
    display: flex; align-items: center; gap: 14px;
    color: var(--text-light);
    font-size: 19px;
    height: 40px;
  }
  .contacts svg { width: 22px; height: 22px; fill: var(--accent); flex: none; }
  .address {
    position: absolute;
    right: 42px; top: 400px;
    text-align: right;
    color: var(--text-light);
    font-size: 19px;
    line-height: 1.45;
  }
</style>
</head>
<body>

  <section class="card card--front" aria-label="Card front">
    <div class="brand"><span class="brand__mark"></span>Brivo Engineering Tandem</div>
  </section>

  <section class="card card--back" aria-label="Card back">
    <div class="holder">
      <p class="holder__name">Helen Marsden</p>
      <p class="holder__role">DIRECTOR</p>
    </div>
    <div class="brand"><span class="brand__mark"></span>Brivo Engineering Tandem</div>
    <div class="divider"></div>
    <ul class="contacts">
      <li>
        <svg viewBox="0 0 24 24" aria-hidden="true"><path d="M3 9c0-3 4-5 9-5s9 2 9 5v2h-5V9c-1-.6-2.4-1-4-1s-3 .4-4 1v2H3z"/><path d="M5 13h14l1 7H4z"/></svg>
        01632 960482
      </li>
      <li>
        <svg viewBox="0 0 24 24" aria-hidden="true"><path d="M2 5h20v14H2z M4 7v.5l8 6 8-6V7z" fill-rule="evenodd"/></svg>
        sales@brivoengineering.co.uk
      </li>
      <li>
        <svg viewBox="0 0 24 24" aria-hidden="true"><path d="M12 2a10 10 0 1 0 0 20 10 10 0 0 0 0-20zm0 2a8 8 0 0 1 7.7 6H16l-2-2h-3l-1 3 3 3v3l-2 3a8 8 0 0 1-7-9l3 2 2-1-1-3 2-3z"/></svg>
        www.brivoengineering.co.uk
      </li>
    </ul>
    <p class="address">Brivo Engineering Tandem<br>22b Corran Way, Kettleby NK4 7RT</p>
  </section>

</body>
</html>
```